Corvane Business Cards

Front of business card will have logo, name, address, & telephone number. Back of card will have a list of services provided - Roads, Substation Pads, Temporary Pads, Site Pads, Land Leveling, Powerline Row Cleaning, Land Clearing, Gates, Fencing, Construction Entrances, Excavation, Trenching, Underground Utilities, Directional Boring, Pile Driving. We are a construction company that uses heavy equipment like bulldozers, motor graders/blades, dump trucks, backhoes, hydro axes, & skid loaders. We build roads, pads, & install electric utility lines & waterlines underground. This logo is new. The word "Construction" can be smaller as uploaded 2 example edited logos. We will be using this card design for many employees.
Target Market(s)
Industrial Electric Powerline, Wind Turbine, Solar Panel, & Water Utility companies.
Contact Information for Business Card
Name/Position - Dwayne Halster - Owner
Address: 4875 FM 309
Merkel, TX 79412
Phone number - (325) 482-5096

```html
<!DOCTYPE html>
<html lang="en">
<head>
<meta charset="utf-8">
<title>Corvane Construction – Business Cards</title>
<link href="https://fonts.googleapis.com/css2?family=Lato:ital,wght@0,400;0,700;0,900;1,400;1,900&display=swap" rel="stylesheet">
<style>
  :root {
    --maroon: #3e1520;
    --maroon-deep: #34111b;
    --paper: #ffffff;
    --ink: #3e1520;
    --ink-soft: #4a3a3e;
    --grey-block: #5c5c5c;
    --stage: #2a2a2a;
    --rule: #b39aa0;
  }
  * { margin: 0; padding: 0; box-sizing: border-box; }
  html, body {
    width: 1200px; height: 878px; overflow: hidden;
    background: var(--stage);
    font-family: "Lato", Arial, sans-serif;
  }
  .canvas { position: relative; width: 1200px; height: 878px; }

  .card {
    position: absolute; left: 280px;
    width: 640px; height: 366px;
    box-shadow: 0 10px 30px rgba(0,0,0,.45);
    overflow: hidden;
  }

  /* Back of card */
  .card-back { top: 48px; background: var(--maroon); color: #fff; }
  .card-back .brand {
    position: absolute; left: 60px; top: 150px; width: 250px;
    display: flex; align-items: center; gap: 12px;
  }
  .brand-mark { width: 16px; height: 16px; flex: none; }
  .card-back .brand-mark { background: #fff; }
  .brand-name {
    font-weight: 700; text-transform: uppercase; letter-spacing: .04em;
    line-height: 1.05;
  }
  .card-back .brand-name { font-size: 26px; color: #fff; }
  .card-back .divider {
    position: absolute; left: 330px; top: 100px;
    width: 1px; height: 166px; background: rgba(255,255,255,.75);
  }
  .services {
    position: absolute; left: 360px; top: 88px;
    list-style: none; font-size: 13.5px; line-height: 21px;
  }
  .services li::before {
    content: ""; display: inline-block; width: 5px; height: 5px;
    border-radius: 50%; background: #fff; margin-right: 9px;
    vertical-align: middle;
  }

  /* Front of card */
  .card-front { top: 462px; background: var(--paper); color: var(--ink); }
  .person { position: absolute; left: 40px; top: 28px; }
  .person-name { font-size: 29px; font-weight: 900; font-style: italic; color: var(--ink); }
  .person-role { font-size: 16px; font-style: italic; color: var(--ink-soft); margin-top: 1px; }

  .card-front .brand {
    position: absolute; right: 36px; top: 150px;
    display: flex; align-items: center; gap: 12px;
  }
  .card-front .brand-mark { background: var(--ink); }
  .card-front .brand-name { font-size: 30px; color: var(--ink); text-align: left; }

  .contacts { position: absolute; left: 40px; top: 210px; list-style: none; }
  .contacts li {
    display: flex; align-items: center; gap: 12px;
    font-size: 17px; color: var(--ink-soft); height: 27px;
  }
  .contacts svg { width: 15px; height: 15px; fill: var(--ink); flex: none; }
  .contact-rule {
    position: absolute; left: 40px; right: 40px; top: 318px;
    height: 1px; background: var(--rule);
  }
  .band {
    position: absolute; left: 0; right: 0; bottom: 0; height: 22px;
    background: var(--maroon-deep);
  }
  .band-accent {
    position: absolute; left: 0; bottom: 22px; width: 58px; height: 14px;
    background: var(--grey-block);
  }
</style>
</head>
<body>
<main class="canvas">

  <section class="card card-back" aria-label="Back of business card">
    <div class="brand">
      <span class="brand-mark"></span>
      <span class="brand-name">Corvane<br>Construction</span>
    </div>
    <div class="divider"></div>
    <ul class="services">
      <li>Roads | Substation Pads</li>
      <li>Temporary Pads | Site Pads</li>
      <li>Land Leveling | Powerline Row Cleaning</li>
      <li>Land Clearing | Gates</li>
      <li>Fencing | Construction Entrances</li>
      <li>Excavation | Trenching</li>
      <li>Underground Utilities | Directional Boring</li>
      <li>Pile Driving</li>
    </ul>
  </section>

  <section class="card card-front" aria-label="Front of business card">
    <div class="person">
      <div class="person-name">Dwayne Halster</div>
      <div class="person-role">Owner</div>
    </div>

    <div class="brand">
      <span class="brand-mark"></span>
      <span class="brand-name">Corvane<br>Construction</span>
    </div>

    <ul class="contacts">
      <li>
        <svg viewBox="0 0 24 24" aria-hidden="true"><path d="M6.6 10.8a15.1 15.1 0 0 0 6.6 6.6l2.2-2.2a1 1 0 0 1 1-.25 11.4 11.4 0 0 0 3.6.57 1 1 0 0 1 1 1V20a1 1 0 0 1-1 1A17 17 0 0 1 3 4a1 1 0 0 1 1-1h3.5a1 1 0 0 1 1 1c0 1.25.2 2.45.57 3.57a1 1 0 0 1-.25 1z"/></svg>
        (325) 482-5096
      </li>
      <li>
        <svg viewBox="0 0 24 24" aria-hidden="true"><path d="M2 5h20v14H2zm2 2v.5l8 5 8-5V7zm0 2.8V17h16V9.8l-8 5z"/></svg>
        info@corvaneconstruction.com
      </li>
      <li>
        <svg viewBox="0 0 24 24" aria-hidden="true"><path d="M12 2a10 10 0 1 0 0 20 10 10 0 0 0 0-20zm6.9 6h-3a15 15 0 0 0-1.3-3.9A8 8 0 0 1 18.9 8zM12 4c.8 1.2 1.5 2.5 1.9 4h-3.8c.4-1.5 1.1-2.8 1.9-4zM4.3 14a8 8 0 0 1 0-4h3.4a16 16 0 0 0 0 4zm.8 2h3a15 15 0 0 0 1.3 3.9A8 8 0 0 1 5.1 16zm3-8h-3a8 8 0 0 1 4.3-3.9A15 15 0 0 0 8.1 8zM12 20c-.8-1.2-1.5-2.5-1.9-4h3.8c-.4 1.5-1.1 2.8-1.9 4zm2.3-6H9.7a14 14 0 0 1 0-4h4.6a14 14 0 0 1 0 4zm.3 5.9a15 15 0 0 0 1.3-3.9h3a8 8 0 0 1-4.3 3.9zm1.7-5.9a16 16 0 0 0 0-4h3.4a8 8 0 0 1 0 4z"/></svg>
        www.corvaneconstruction.com
      </li>
      <li>
        <svg viewBox="0 0 24 24" aria-hidden="true"><path d="M12 2a7 7 0 0 0-7 7c0 5.2 7 13 7 13s7-7.8 7-13a7 7 0 0 0-7-7zm0 9.5A2.5 2.5 0 1 1 12 6.5a2.5 2.5 0 0 1 0 5z"/></svg>
        4875 FM 309 Merkel, TX 79412
      </li>
    </ul>
    <div class="contact-rule"></div>
    <div class="band-accent"></div>
    <div class="band"></div>
  </section>

</main>
</body>
</html>
```